Need Web Design for Business Process Outsourcing Company (Quorvane)

Quorvane is a business process outsourcing company. Need a simple site similar to http://www.tallowbrinkhire.com/ but with a more professional and credible look. New to the process; not sure where to start and comparing my options. Please let me know what my options are if I choose to go with you. Logo is attached for your reference. Please use same colorway

Reason: I want the final product to be coded. Please confirm you will be able to code final design.

Industry/Entity Type

Business

Coding

Coded - Design and coding required

```html
<!DOCTYPE html>
<html lang="en">
<head>
<meta charset="utf-8">
<title>Quorvane – Business Process Outsourcing</title>
<link href="https://fonts.googleapis.com/css2?family=Roboto+Slab:wght@300;400;500&family=Arimo:wght@400;700&display=swap" rel="stylesheet">
<style>
:root{
  --blue:#0a8bd1;
  --blue-deep:#0d5a8e;
  --navy:#1d4f78;
  --ink:#333;
  --muted:#555;
  --nav-active:#3b3b3b;
  --rule:#e2e2e2;
  --grey-bg:#f1f1f1;
  --white:#fff;
}
*{margin:0;padding:0;box-sizing:border-box}
html,body{width:1200px;height:3321px;overflow:hidden;background:var(--white)}
body{position:relative;font-family:"Roboto Slab",Georgia,serif;color:var(--ink)}
.abs{position:absolute}
a{color:inherit;text-decoration:none}

/* header */
.brand{display:flex;align-items:center;gap:10px;font-family:"Roboto Slab",serif;font-weight:500;color:var(--navy)}
.brand-mark{width:34px;height:34px;background:var(--blue)}
.site-header .brand{left:100px;top:26px;font-size:30px}
.search{left:726px;top:31px;width:204px;height:33px;border:1px solid #ddd;font-family:Arimo,sans-serif;font-size:12px;color:#aaa;padding:9px 10px}
.search-btn{left:939px;top:31px;width:37px;height:33px;background:#333}
.chat-btn{left:994px;top:31px;width:106px;height:33px;background:var(--blue-deep);color:#fff;font-family:Arimo,sans-serif;font-weight:700;font-size:12px;display:flex;align-items:center;justify-content:center;gap:6px}

.main-nav{left:0;top:97px;width:1200px;height:71px;background:var(--blue)}
.main-nav a{position:absolute;top:0;height:71px;line-height:71px;font-size:13px;color:#fff;transform:translateX(-50%);white-space:nowrap}
.main-nav .active{left:100px;width:95px;transform:none;text-align:center;background:var(--nav-active)}

/* hero */
.hero-title{left:872px;top:450px;width:228px;text-align:right;font-size:44px;color:#fff;font-weight:400}
.hero-text{left:790px;top:522px;width:310px;text-align:right;font-size:12.5px;line-height:22px;color:#fff}
.dot{top:694px;width:20px;height:20px;border:2px solid #fff;border-radius:50%}

/* sections */
.section-title{left:0;width:1200px;text-align:center;font-size:26px;color:var(--blue);font-weight:400;letter-spacing:1px}
.section-lead{left:260px;width:680px;text-align:center;font-size:12.5px;line-height:22px;color:var(--muted)}

.service{width:320px;text-align:center}
.service .disc{width:110px;height:110px;border-radius:50%;background:var(--blue-deep);margin:0 auto;display:flex;align-items:center;justify-content:center}
.service h3{margin-top:32px;font-family:Arimo,sans-serif;font-weight:400;font-size:17px;color:#222}
.service p{margin:22px auto 0;width:260px;font-size:12.5px;line-height:22px;color:var(--muted)}

.bpo-photo{left:0;top:1242px;width:600px;height:438px;background:linear-gradient(135deg,#d8dadc 0%,#c3c6c8 40%,#e6e6e4 70%,#b9bcbe 100%)}
.bpo-panel{left:600px;top:1242px;width:600px;height:438px;background:var(--blue);color:#fff}
.bpo-panel h2{position:absolute;left:55px;top:58px;font-size:24px;font-weight:400}
.bpo-panel p{position:absolute;left:55px;top:116px;width:500px;font-size:12.5px;line-height:22.5px}
.btn-outline{position:absolute;left:55px;top:332px;width:124px;height:44px;border:1px solid #fff;color:#fff;font-family:Arimo,sans-serif;font-weight:700;font-size:12px;display:flex;align-items:center;justify-content:center}

.feature .ring{position:absolute;left:0;top:0;width:80px;height:80px;border-radius:50%;border:1px solid #ccc;display:flex;align-items:center;justify-content:center;background:#fff}
.feature .ring.filled{background:var(--blue);border-color:var(--blue)}
.feature h3{position:absolute;left:106px;top:26px;white-space:nowrap;font-family:Arimo,sans-serif;font-weight:400;font-size:19px;color:var(--navy)}
.feature p{position:absolute;left:0;top:102px;width:320px;font-family:Arimo,sans-serif;font-size:12.5px;line-height:22px;color:#333}

.news-band{left:0;top:2271px;width:1200px;height:662px;background:var(--grey-bg)}
.post-photo{width:460px;height:221px;border:4px solid #fff;box-shadow:0 0 0 1px #ddd}
.post h3{position:absolute;top:257px;left:0;font-size:16px;font-weight:400;color:#222;white-space:nowrap}
.post .meta{position:absolute;top:284px;left:0;font-family:Arimo,sans-serif;font-size:11.5px;color:#333}
.post .meta b{color:var(--blue);font-weight:400}
.post p{position:absolute;top:312px;left:0;width:460px;font-size:12.5px;line-height:22px;color:var(--muted)}
.pill{position:absolute;top:403px;left:0;width:99px;height:31px;border:1px solid var(--blue);border-radius:16px;color:var(--blue-deep);font-family:Arimo,sans-serif;font-size:11.5px;display:flex;align-items:center;justify-content:center}

/* footer */
.site-footer .brand{left:100px;top:3076px;font-size:30px}
.foot-head{font-size:18px;font-weight:400;color:#222;letter-spacing:1px}
.foot-head::after{content:"";display:block;width:34px;height:2px;background:var(--blue);margin-top:8px}
.foot-list{list-style:none;width:140px}
.foot-list li{font-size:12px;color:#444;height:34.5px;line-height:34.5px;border-bottom:1px solid var(--rule)}
.contact-list{width:196px}
.email{left:830px;top:3115px;width:220px;height:42px;border:1px solid #ddd;font-size:12px;color:#aaa;padding:13px 12px;background:#fff}
.email-btn{left:1050px;top:3115px;width:50px;height:42px;background:var(--blue);display:flex;align-items:center;justify-content:center}
.social{top:3189px;width:30px;height:30px;border-radius:50%}

.bottom-bar{left:0;top:3263px;width:1200px;height:58px;background:linear-gradient(#cfcfcf,#a9a9a9);font-family:Arimo,sans-serif;font-size:12px;color:#fff}
.bottom-bar span{position:absolute;top:22px;white-space:nowrap}
</style>
</head>
<body>

<header class="site-header">
  <div class="abs brand"><span class="brand-mark"></span>Quorvane</div>
  <div class="abs search">Search...</div>
  <div class="abs search-btn">
    <svg width="37" height="33" viewBox="0 0 37 33"><circle cx="17" cy="15" r="4.5" fill="none" stroke="#fff" stroke-width="2"/><line x1="20.5" y1="18.5" x2="24" y2="22" stroke="#fff" stroke-width="2"/></svg>
  </div>
  <div class="abs chat-btn">
    <svg width="16" height="13" viewBox="0 0 16 13"><path d="M1 1h10v7H5l-3 3V8H1z" fill="#fff"/><path d="M12 4h3v6h-1v2l-2-2H7V9h5z" fill="#fff"/></svg>Live Chat
  </div>
</header>

<nav class="abs main-nav">
  <a class="active" href="#">HOME</a>
  <a style="left:275px" href="#">WHO WE ARE</a>
  <a style="left:436px" href="#">OUR SOLUTIONS</a>
  <a style="left:602px" href="#">OUR STRATEGY</a>
  <a style="left:773px" href="#">OUR EXPERIENCE</a>
  <a style="left:925px" href="#">SECURITY</a>
  <a style="left:1060px" href="#">CONTACT US</a>
</nav>

<section class="hero">
  <svg class="abs" style="left:0;top:168px" width="1200" height="574" viewBox="0 0 1200 574" role="img" aria-label="Photo of two colleagues shaking hands across a desk with a laptop and coffee cup">
    <defs>
      <linearGradient id="heroTone" x1="0" y1="0" x2="1" y2="1">
        <stop offset="0" stop-color="#6f6d6a"/>
        <stop offset=".35" stop-color="#3e3c3b"/>
        <stop offset=".7" stop-color="#2b2a2a"/>
        <stop offset="1" stop-color="#4a4846"/>
      </linearGradient>
    </defs>
    <path d="M0 0H1200V496Q600 640 0 496Z" fill="url(#heroTone)"/>
  </svg>
  <h1 class="abs hero-title">QUORVANE</h1>
  <p class="abs hero-text">There are many variations of passages of Lorem Ipsum available, but the majority have suffered alteration in which don't look even slightly believable.</p>
  <span class="abs dot" style="left:543px"></span>
  <span class="abs dot" style="left:588px"></span>
  <span class="abs dot" style="left:632px"></span>
</section>

<section class="services">
  <h2 class="abs section-title" style="top:806px">QUORVANE &nbsp;SERVICES</h2>
  <p class="abs section-lead" style="top:855px">There are many variations of passages of Lorem Ipsum available, but the majority have suffered alteration in some form, by injected humour, or randomised words which don't look even slightly believable.</p>

  <div class="abs service" style="left:59px;top:941px">
    <div class="disc"><svg width="44" height="40" viewBox="0 0 44 40"><path d="M4 14h8l16-9v30l-16-9H4z" fill="#fff"/><rect x="8" y="26" width="6" height="10" fill="#fff"/><path d="M32 13q5 7 0 14" stroke="#fff" stroke-width="3" fill="none"/></svg></div>
    <h3>Customer Service</h3>
    <p>There are many variations of passages of Lorem Ipsum available, but the majority have suffered alteration in</p>
  </div>
  <div class="abs service" style="left:440px;top:941px">
    <div class="disc"><svg width="38" height="34" viewBox="0 0 38 34"><path d="M2 4h6l4 18h18l4-13H10" stroke="#fff" stroke-width="3" fill="none"/><path d="M11 9h22l-3 11H13z" fill="#fff"/><circle cx="14" cy="29" r="3" fill="#fff"/><circle cx="28" cy="29" r="3" fill="#fff"/></svg></div>
    <h3>Ecommerce</h3>
    <p>There are many variations of passages of Lorem Ipsum available, but the majority have suffered alteration in</p>
  </div>
  <div class="abs service" style="left:819px;top:941px">
    <div class="disc"><svg width="30" height="42" viewBox="0 0 30 42"><circle cx="15" cy="14" r="11" stroke="#fff" stroke-width="3" fill="none"/><rect x="9" y="27" width="12" height="4" fill="#fff"/><rect x="10" y="33" width="10" height="3" fill="#fff"/><path d="M11 14q0-4 4-4" stroke="#fff" stroke-width="2" fill="none"/></svg></div>
    <h3>IT Solutions</h3>
    <p>There are many variations of passages of Lorem Ipsum available, but the majority have suffered alteration in</p>
  </div>
</section>

<section class="bpo">
  <div class="abs bpo-photo" role="img" aria-label="Top-down photo of a white office desk with keyboard, laptop, tablet, camera, glasses and a plant"></div>
  <div class="abs bpo-panel">
    <h2>BPO Business Process</h2>
    <p>There are many variations of passages of Lorem Ipsum available, but the majority have suffered alteration in some form, by injected humour, or randomised words which don't look even slightly believable. If you are going to use a passage of Lorem Ipsum, you need to be sure there isn't anything embarrassing hidden in the middle of text. All the Lorem Ipsum generators on the Internet tend to repeat predefined chunks as necessary, making this the first true generator on the Internet. It uses a dictionary of over 200 Latin words, combined with a handful of model sentence structures, to generate Lorem Ipsum</p>
    <a class="btn-outline" href="#">LEARN MORE</a>
  </div>
</section>

<section class="featured">
  <h2 class="abs section-title" style="top:1722px">OUR FEATURED</h2>
  <p class="abs section-lead" style="top:1767px;font-family:Arimo,sans-serif;color:#444">Technologists, as a practice, have strayed from the fundamental principles that have driven much<br>of the innovation that has gotten us to where we are</p>

  <div class="abs feature" style="left:100px;top:1855px">
    <div class="ring"><svg width="26" height="30" viewBox="0 0 26 30"><rect x="3" y="2" width="20" height="26" fill="none" stroke="#0a8bd1" stroke-width="2"/><path d="M8 9h10M8 14h10M8 19h6" stroke="#0a8bd1" stroke-width="2"/></svg></div>
    <h3>OUR SERVICES TEXT</h3>
    <p>Today Solution Architecture is more about pre-sales of a canned solution hacked sideways into a the larger enterprise than it is about utilizing the tools.</p>
  </div>
  <div class="abs feature" style="left:449px;top:1855px">
    <div class="ring filled"><svg width="30" height="30" viewBox="0 0 30 30"><ellipse cx="13" cy="7" rx="9" ry="3.5" fill="#fff"/><path d="M4 11q9 5 18 0v4q-9 5-18 0zM4 18q9 5 18 0v4q-9 5-18 0z" fill="#fff"/><circle cx="23" cy="22" r="6" fill="#fff"/><path d="M23 19v6M20 22h6" stroke="#0a8bd1" stroke-width="2"/></svg></div>
    <h3>OUR SERVICES TEXT</h3>
    <p>Today Solution Architecture is more about pre-sales of a canned solution hacked sideways into a the larger enterprise than it is about utilizing the tools.</p>
  </div>
  <div class="abs feature" style="left:797px;top:1855px">
    <div class="ring"><svg width="30" height="30" viewBox="0 0 30 30"><rect x="3" y="7" width="18" height="20" fill="none" stroke="#0a8bd1" stroke-width="2"/><rect x="9" y="3" width="18" height="20" fill="#fff" stroke="#0a8bd1" stroke-width="2"/><path d="M13 9h10M13 13h10M13 17h6" stroke="#0a8bd1" stroke-width="2"/></svg></div>
    <h3>OUR SERVICES TEXT</h3>
    <p>Today Solution Architecture is more about pre-sales of a canned solution hacked sideways into a the larger enterprise than it is about utilizing the tools.</p>
  </div>

  <div class="abs feature" style="left:100px;top:2054px">
    <div class="ring"><svg width="32" height="30" viewBox="0 0 32 30"><rect x="3" y="4" width="22" height="16" fill="none" stroke="#0a8bd1" stroke-width="2"/><path d="M10 26h8M14 20v6" stroke="#0a8bd1" stroke-width="2"/><circle cx="24" cy="19" r="5" fill="#0a8bd1"/><circle cx="24" cy="19" r="2" fill="#fff"/></svg></div>
    <h3>OUR SERVICES TEXT</h3>
    <p>Today Solution Architecture is more about pre-sales of a canned solution hacked sideways into a the larger enterprise than it is about utilizing the tools.</p>
  </div>
  <div class="abs feature" style="left:449px;top:2054px">
    <div class="ring"><svg width="26" height="32" viewBox="0 0 26 32"><path d="M9 16V4a2 2 0 0 1 4 0v10l8 2q3 1 2 5l-2 8H11l-6-8q-1-3 2-3z" fill="none" stroke="#0a8bd1" stroke-width="2"/></svg></div>
    <h3>OUR SERVICES TEXT</h3>
    <p>Today Solution Architecture is more about pre-sales of a canned solution hacked sideways into a the larger enterprise than it is about utilizing the tools.</p>
  </div>
  <div class="abs feature" style="left:797px;top:2054px">
    <div class="ring"><svg width="34" height="24" viewBox="0 0 34 24"><path d="M2 8l7-5 8 4 8-4 7 5-9 9q-2 2-4 0l-4-4M2 8l8 9" fill="none" stroke="#0a8bd1" stroke-width="2.2"/></svg></div>
    <h3>OUR SERVICES TEXT</h3>
    <p>Today Solution Architecture is more about pre-sales of a canned solution hacked sideways into a the larger enterprise than it is about utilizing the tools.</p>
  </div>
</section>

<section class="news">
  <div class="abs news-band"></div>
  <h2 class="abs section-title" style="top:2317px">NEWS &amp; BLOG</h2>
  <p class="abs section-lead" style="top:2362px;font-family:Arimo,sans-serif;color:#444">Technologists, as a practice, have strayed from the fundamental principles that have driven much<br>of the innovation that has gotten us to where we are</p>

  <article class="abs post" style="left:100px;top:2442px;width:460px">
    <div class="post-photo" role="img" aria-label="Overhead photo of a team joining hands above a meeting table" style="background:linear-gradient(135deg,#4a3a2e,#7a6652 50%,#3a2f27)"></div>
    <h3>Corporate immigration service provider</h3>
    <div class="meta">Posted By : <b>Delwyn</b> &nbsp;| Date : <b>20.11.2016</b></div>
    <p>Lorem Ipsum is that it has a more-or-less normal distribution of letters as opposed to using Content here, content here', making it look like readable English. Many desktop publishing packages and web page editors now use.</p>
    <a class="pill" href="#">READ MORE</a>
  </article>
  <article class="abs post" style="left:638px;top:2442px;width:460px">
    <div class="post-photo" role="img" aria-label="Photo of hands reviewing financial charts on paper beside a laptop" style="background:linear-gradient(135deg,#f3e4cf,#d9dde2 50%,#9fb0c2)"></div>
    <h3>Corporate immigration service provider</h3>
    <div class="meta">Posted By : <b>Delwyn</b> &nbsp;| Date : <b>20.11.2016</b></div>
    <p>Lorem Ipsum is that it has a more-or-less normal distribution of letters as opposed to using Content here, content here', making it look like readable English. Many desktop publishing packages and web page editors now use.</p>
    <a class="pill" href="#">READ MORE</a>
  </article>
</section>

<footer class="site-footer">
  <div class="abs brand"><span class="brand-mark"></span>Quorvane</div>

  <div class="abs" style="left:354px;top:2992px">
    <h4 class="foot-head">OUR LINK</h4>
    <ul class="foot-list" style="margin-top:20px">
      <li>Who We Are</li><li>Our Solutions</li><li>Our Strategy</li><li>Our Experience</li><li>Security</li>
    </ul>
  </div>

  <div class="abs" style="left:558px;top:2992px">
    <h4 class="foot-head">CONTACT</h4>
    <ul class="foot-list contact-list" style="margin-top:20px">
      <li>(555) 014 2270 &nbsp;( Office )</li>
      <li>(555) 018 3394 &nbsp;( Cell )</li>
      <li>www.quorvane.com</li>
      <li style="line-height:19px;padding-top:6px;height:48px;border:0">#000 – Our Street, Our City, company Country</li>
    </ul>
  </div>

  <div class="abs" style="left:830px;top:2992px">
    <h4 class="foot-head">NEWSLETTER SIGNUP</h4>
    <p style="margin-top:20px;width:270px;font-size:12px;line-height:19px;color:#444">There are many variations of passages of Lorem available, but the majority</p>
  </div>
  <div class="abs email">Email Addres</div>
  <div class="abs email-btn"><svg width="18" height="18" viewBox="0 0 18 18"><path d="M1 8L17 1 12 17 9 10z" fill="#fff"/></svg></div>
  <span class="abs social" style="left:831px;background:#3b5998"></span>
  <span class="abs social" style="left:875px;background:#1da1f2"></span>
  <span class="abs social" style="left:919px;background:#dd4b39"></span>

  <div class="abs bottom-bar">
    <span style="left:100px">Copyright © 2016. Quorvane.com</span>
    <span style="left:617px">Terms of Use</span>
    <span style="left:728px">Legal disclaimer</span>
    <span style="left:860px">Privacy Policy</span>
    <span style="left:973px">Support</span>
    <span style="left:1052px">Sitemap</span>
  </div>
</footer>

</body>
</html>
```